Tessmar Fahrwerkstatt
Sehr angenehme zusammenarbeit nicht aufdringlich und genau auf die Wünsche eingegangen. Wir werde sicher noch mehr zusammen Arbeiten. Gruss Lukas Hegemann Inhaber Tessmar Fahrwerkstatt
Zielgruppe
Dinks und Kunden mit viel Erfolg und hohem Ausgabepotential.
Aufgabenstellung
Unsere Firma vertreibt Fahrzeuge im Luxusbereich hauptgebiet Valmerra aber auch andere Sportwagen. Was uns fehlt ist ein optischer Wiedererkennugswert. Deshalb hätten wir gerne ein Visitenkarten Design und Briefpapier Design. Später soll auch noch eine Webseite mit gleichem Wiedererkennungswert entstehen. " Roter Faden "

```html
<!DOCTYPE html>
<html lang="de">
<head>
<meta charset="utf-8">
<title>Tessmar Fahrwerkstatt – Visitenkarte</title>
<link rel="stylesheet" href="https://fonts.googleapis.com/css2?family=Tenor+Sans&display=swap">
<style>
  :root {
    --page-bg: #e6e6e4;
    --card-top: #3b3e43;
    --card-deep: #0d0e10;
    --band-white: #ffffff;
    --slate: #435066;
    --slate-light: #6b7688;
    --slate-dark: #3a465a;
    --brand-text: #ffffff;
    --brand-dot: #c9ccd1;
  }
  html, body {
    margin: 0;
    padding: 0;
    width: 1200px;
    height: 910px;
    overflow: hidden;
    background: var(--page-bg);
  }
  .business-card {
    position: absolute;
    left: 90px;
    top: 115px;
    width: 1020px;
    height: 680px;
    overflow: hidden;
  }
  .card-art {
    position: absolute;
    inset: 0;
    display: block;
  }
  .brand {
    position: absolute;
    left: 212px;
    top: 150px;
    display: flex;
    align-items: center;
    gap: 46px;
  }
  .brand-dot {
    width: 104px;
    height: 104px;
    border-radius: 50%;
    background: var(--brand-dot);
    flex: none;
  }
  .brand-name {
    margin: 0;
    font-family: "Tenor Sans", sans-serif;
    font-weight: 400;
    font-size: 52px;
    line-height: 1.22;
    letter-spacing: 1px;
    color: var(--brand-text);
    text-transform: uppercase;
  }
  .brand-name span { display: block; }
</style>
</head>
<body>
  <main class="business-card">
    <svg class="card-art" viewBox="0 0 1020 680" width="1020" height="680" aria-hidden="true">
      <defs>
        <linearGradient id="dark-field" x1="0" y1="0" x2="0" y2="1">
          <stop offset="0" stop-color="var(--card-top)"/>
          <stop offset="0.75" stop-color="var(--card-deep)"/>
        </linearGradient>
        <radialGradient id="slate-field" cx="0.5" cy="0.55" r="0.6">
          <stop offset="0" stop-color="var(--slate-light)"/>
          <stop offset="0.55" stop-color="var(--slate)"/>
          <stop offset="1" stop-color="var(--slate-dark)"/>
        </radialGradient>
      </defs>
      <rect class="dark-field" width="1020" height="680" fill="url(#dark-field)"/>
      <path class="white-band" d="M0,488 C260,380 600,355 1020,352 L1020,680 L0,680 Z" fill="var(--band-white)"/>
    </svg>
    <svg class="card-art" viewBox="0 0 1020 680" width="1020" height="680" role="img" aria-label="Dekoratives Muster aus feinen, geschwungenen Linien auf schieferblauem Grund">
      <path class="slate-field" d="M0,535 C300,430 620,395 1020,390 L1020,680 L0,680 Z" fill="url(#slate-field)"/>
    </svg>
    <div class="brand">
      <div class="brand-dot"></div>
      <h1 class="brand-name"><span>Tessmar</span><span>Fahrwerkstatt</span></h1>
    </div>
  </main>
</body>
</html>
```